Distribution/Printing company needs a web site to inform prospective customers on what we do.

Distribution/Printing/Packaging company needs a web site to inform prospective customers on what we do. Please look at our direct to consumer web site (under development) for an idea of the product lines we sell: storedev.maplewickhaven.com
Logo files are attached as is a flyer that is under development which contains other information about the company (this is to be used for content- not to be posted as is). The web site should be focused on our business customer base and is not intended to be direct to consumer. Site should have a link to our consumer web site.
Site design should be mobile friendly, or mobile could be redirected to a mobile version. This web site will be strictly informational and will not be designed for any sales transactions.

Target Market(s)

Manufacturing and retail businesses, any other multi-site business that would benefit from centralized pricing and budget controls we can provide (banks, medical/dental offices, educational facilities, etc).

Industry/Entity Type

It Company

Coding

Coded - Design and coding required

Number of Pages Required

5+ page

Requirements
Must have
• 1) Top level menu: Products, about us, locations, contact us, news
• 2) page with news/promotions that is easily updated
• 3) "contact us" form (name, company, phone, email address) email link
• 4) link to www.store.maplewickhaven.com with information that lower pricing is available for businesses
• 5) SEO keywords
• 6) Link to powerpoint presentation file
Nice to have
• 1) our phone number should appear on every page near the top

```html
<!DOCTYPE html>
<html lang="en">
<head>
<meta charset="utf-8">
<title>Harbor Lane Supply – Packaging, Printing, Distribution</title>
<link rel="stylesheet" href="https://fonts.googleapis.com/css2?family=Arimo:wght@400;700&family=PT+Sans:wght@400;700&display=swap">
<style>
:root{
  --orange:#f0a21d;
  --orange-deep:#f06a2b;
  --red:#e8513a;
  --brown:#a47b5a;
  --brown-foot:#8d6a4f;
  --brown-dark:#6b4c36;
  --ink:#1f1f1f;
  --text:#3a3a3a;
  --muted:#6a6a6a;
  --line:#d8d8d8;
  --panel:#f7f7f7;
  --white:#ffffff;
}
*{box-sizing:border-box;margin:0;padding:0}
html,body{width:1200px;height:1189px;overflow:hidden}
body{font-family:"Arimo",Arial,sans-serif;color:var(--text);background:var(--white);position:relative}
.top-band{position:absolute;left:0;top:0;width:1200px;height:277px;background:linear-gradient(#e4e4e4,#f6f6f6 40%,#efefef)}
.page{position:absolute;left:224px;top:0;width:752px;height:1189px}
.abs{position:absolute}

.brand{left:3px;top:22px;width:200px}
.brand-name{font-family:"PT Sans",sans-serif;font-weight:700;font-size:17px;color:var(--ink);letter-spacing:.5px;display:flex;align-items:center;gap:8px;margin-top:34px}
.brand-name .mark{width:14px;height:14px;background:var(--ink)}
.brand-tag{font-size:11px;font-weight:700;color:var(--ink);margin-top:3px;letter-spacing:.2px}

.call-box{left:516px;top:13px;width:236px;height:51px;background:var(--brown);border-radius:4px;color:var(--white);padding:6px 0 0 14px}
.call-row{display:flex;align-items:center;gap:10px}
.call-phone{font-family:"PT Sans",sans-serif;font-weight:700;font-size:17px}
.call-mail{font-size:12px;margin-top:2px}

.main-nav{left:0;top:123px;width:752px;height:40px;background:var(--orange);display:flex;align-items:center}
.nav-home{width:33px;height:40px;background:var(--red);display:flex;align-items:center;justify-content:center}
.nav-link{color:var(--white);font-size:14px;margin-left:17px;margin-right:10px}
.nav-delivery{position:absolute;right:0;top:0;width:170px;height:40px;background:var(--brown);border-radius:20px 0 0 20px;display:flex;align-items:center;gap:8px;padding-left:22px;color:var(--white);font-size:11px;font-weight:700}

.hero{left:0;top:163px;width:508px;height:234px;background:linear-gradient(90deg,#f2ebe4 0%,#efe6dc 45%,#e9ddcf 70%,#d7b9a6 100%)}
.hero-photo{position:absolute;right:0;top:0;width:300px;height:234px;background:radial-gradient(circle at 60% 40%,#e44a3a 0 14%,#efe3d6 15% 40%,transparent 60%),linear-gradient(120deg,#e9ddd0,#cdb6a0)}
.hero-copy{position:absolute;left:22px;top:56px;width:270px}
.hero-title{font-family:"PT Sans",sans-serif;font-weight:400;font-size:26px;line-height:30px;color:var(--ink)}
.hero-text{font-size:10px;line-height:13px;color:var(--muted);margin-top:6px}
.hero-actions{display:flex;gap:10px;margin-top:20px}
.btn{height:24px;border-radius:3px;font-size:11px;display:flex;align-items:center;justify-content:center}
.btn-grey{width:84px;background:linear-gradient(#f2f2f2,#c9c9c9);color:var(--ink);border:1px solid #b9b9b9}
.btn-orange{width:84px;background:linear-gradient(#ff8a4c,var(--orange-deep));color:var(--white)}

.quote{left:509px;top:168px;width:243px;height:380px;background:var(--panel);border:1px solid #f4b870;border-radius:3px;overflow:hidden}
.quote-head{height:37px;background:linear-gradient(#ff8a50,var(--orange-deep));color:var(--white);font-family:"PT Sans",sans-serif;font-size:18px;display:flex;align-items:center;justify-content:center}
.quote-form{padding:11px 10px 0 10px}
.field{height:29px;border:1px solid #cfcfcf;background:var(--white);border-radius:2px;margin-bottom:3px;font-size:11px;color:var(--ink);padding-left:7px;display:flex;align-items:center;justify-content:space-between;padding-right:8px}
.req{color:var(--red)}
.quote-submit{margin-top:9px;height:38px;border-radius:4px;background:linear-gradient(#ff8f55,var(--orange-deep));color:var(--white);font-family:"PT Sans",sans-serif;font-size:16px;display:flex;align-items:center;justify-content:center;text-transform:uppercase}
.quote-note{font-size:9px;font-style:italic;text-align:center;margin-top:12px;color:var(--ink);font-weight:700}

.welcome{left:0;top:407px;width:497px;height:140px;background:var(--panel);border:1px solid var(--line);border-radius:3px}
.welcome-title{margin:10px 0 0 0;border-left:4px solid var(--orange);padding-left:12px;font-size:12px;font-weight:700;color:var(--ink);height:24px;display:flex;align-items:center}
.welcome-text{font-size:10px;line-height:16px;color:var(--muted);padding:8px 16px 0 16px}
.more{position:absolute;right:16px;bottom:8px;font-size:8px;font-weight:700;color:var(--orange-deep)}

.card{top:559px;width:241px;height:237px;background:var(--panel);border:1px solid var(--line);border-radius:3px}
.card-head{height:35px;background:linear-gradient(#fdfdfd,#e3e3e3);border-bottom:1px solid var(--line);font-size:13px;color:var(--ink);display:flex;align-items:center;justify-content:center}
.card-photo{margin:8px 0 0 17px;width:206px;height:88px}
.card-list{list-style:none;padding:8px 12px 0 17px}
.card-list li{display:flex;gap:9px;font-size:10px;line-height:13px;color:var(--text);margin-bottom:8px}
.dot{flex:0 0 9px;height:9px;border:1px solid #999;border-radius:50%;margin-top:2px}
.quote-mark{font-family:"PT Sans",sans-serif;font-size:22px;line-height:14px;color:var(--ink)}
.testi{display:flex;gap:6px;padding:9px 14px 0 9px;font-size:10px;line-height:14px}
.testi-name{font-size:10px;font-weight:700;color:var(--ink);padding:10px 0 0 26px}

.divider{left:0;top:822px;width:752px;height:10px;background:radial-gradient(ellipse at 50% 0,rgba(0,0,0,.18),transparent 70%)}
.clients-title{left:0;top:842px;width:752px;text-align:center;font-size:13px;color:var(--ink);letter-spacing:.5px}
.clients{left:100px;top:886px;width:560px;display:flex;justify-content:space-between}
.client{display:flex;align-items:center;gap:5px;font-size:12px;font-weight:700;color:var(--ink)}
.client .c{width:12px;height:12px;border-radius:50%;background:var(--ink)}

.footer{position:absolute;left:0;top:956px;width:1200px;height:213px;background:var(--brown-foot);color:var(--white)}
.footer-bottom{position:absolute;left:0;top:1169px;width:1200px;height:20px;background:var(--brown-dark);color:var(--white);font-size:11px;text-align:center;line-height:20px}
.fcol{position:absolute;top:34px}
.fcol h3{font-size:13px;font-weight:400;margin-bottom:14px}
.contact-row{display:flex;gap:8px;font-size:10px;line-height:14px;margin-bottom:5px}
.links li{list-style:none;font-size:10px;line-height:15px}
.socials{display:flex;gap:3px}
.socials span{width:19px;height:19px;border-radius:2px}
.like{margin-top:12px;width:74px;height:22px;background:var(--white);border:1px solid #ccc;border-radius:3px;color:var(--ink);font-size:9px;display:flex;align-items:center;justify-content:space-around}
.finput{width:184px;height:23px;background:#ececec;border:1px solid #cfcfcf;border-radius:2px;color:var(--ink);font-size:9px;padding:4px 8px;margin-bottom:5px}
.fsubmit{margin:9px 0 0 96px;width:88px;height:30px;border-radius:3px;background:linear-gradient(#ff8f55,var(--orange-deep));font-size:12px;display:flex;align-items:center;justify-content:center}
</style>
</head>
<body>
<div class="top-band"></div>

<div class="page">
  <div class="abs brand">
    <div class="brand-name"><span class="mark"></span>HARBOR LANE SUPPLY</div>
    <div class="brand-tag">Packaging • Printing • Distribution</div>
  </div>

  <div class="abs call-box">
    <div class="call-row">
      <svg width="14" height="14" viewBox="0 0 24 24"><path fill="#fff" d="M6.6 10.8a15 15 0 0 0 6.6 6.6l2.2-2.2a1 1 0 0 1 1-.25 11 11 0 0 0 3.6.6 1 1 0 0 1 1 1V20a1 1 0 0 1-1 1A17 17 0 0 1 3 4a1 1 0 0 1 1-1h3.5a1 1 0 0 1 1 1c0 1.25.2 2.45.6 3.6a1 1 0 0 1-.25 1z"/></svg>
      <span class="call-phone">Call Us: (416) 555-0148</span>
    </div>
    <div class="call-row call-mail">
      <svg width="12" height="10" viewBox="0 0 24 18"><rect width="24" height="18" rx="2" fill="#fff"/><path d="M1 2l11 8 11-8" stroke="#a47b5a" stroke-width="2" fill="none"/></svg>
      <span>info@harborlaneSupply.com</span>
    </div>
  </div>

  <nav class="abs main-nav">
    <span class="nav-home"><svg width="14" height="13" viewBox="0 0 24 22"><path fill="#fff" d="M12 0 0 11h3v11h7v-7h4v7h7V11h3z"/></svg></span>
    <span class="nav-link">Packaging</span>
    <span class="nav-link">Office Supplies</span>
    <span class="nav-link">Janitorial</span>
    <span class="nav-link">Retail Supplies</span>
    <span class="nav-link">Contact US</span>
    <span class="nav-delivery"><svg width="26" height="26" viewBox="0 0 26 26"><rect x="2" y="4" width="22" height="18" fill="#f5f0ea"/><rect x="9" y="4" width="8" height="6" fill="#c9b49e"/></svg>Free pickup &amp; Delivery</span>
  </nav>

  <section class="abs hero">
    <div class="hero-photo" role="img" aria-label="Photo of rolled printed paper stock with red cores"></div>
    <div class="hero-copy">
      <h1 class="hero-title">High-quality product under strict deadlines</h1>
      <p class="hero-text">Etultrices posuere cubilia Curae; Suspendisse a tellus quis libero euismod egestas nam.dolor mauris.</p>
      <div class="hero-actions"><span class="btn btn-grey">Learn more</span><span class="btn btn-orange">Get Quote</span></div>
    </div>
  </section>

  <aside class="abs quote">
    <div class="quote-head">Get Quote</div>
    <div class="quote-form">
      <div class="field"><span>Enter name<span class="req">*</span></span></div>
      <div class="field"><span>Company</span></div>
      <div class="field"><span>Country</span></div>
      <div class="field"><span>Address <span class="req">*</span></span></div>
      <div class="field"><span>Email <span class="req">*</span></span></div>
      <div class="field"><span>Mobile number <span class="req">*</span></span></div>
      <div class="field"><span>Type of service I want <span class="req">*</span></span><svg width="10" height="7" viewBox="0 0 10 7"><path d="M1 1l4 4 4-4" stroke="#222" stroke-width="2" fill="none"/></svg></div>
      <div class="field"><span>Upload a file</span><svg width="11" height="11" viewBox="0 0 12 12"><circle cx="5" cy="5" r="3.5" stroke="#b07a3a" stroke-width="2" fill="none"/><path d="M8 8l3 3" stroke="#b07a3a" stroke-width="2"/></svg></div>
      <div class="quote-submit">Submit my quote</div>
      <p class="quote-note">Field marked with * are mandatory</p>
    </div>
  </aside>

  <section class="abs welcome">
    <h2 class="welcome-title">Welocme to&nbsp; Harbor Lane Supply.</h2>
    <p class="welcome-text">We maintain absolute integrity in every aspect of our operation. By using our experience to understand our customers' expectations, we show an uncommon commitment to achieving a high-quality product under strict deadlines. It is the customers who set the standards we strive to achieve. We are professionals who bring unique and specialized skills you can depend on.</p>
    <span class="more">Read more</span>
  </section>

  <section class="abs card" style="left:0">
    <h3 class="card-head">Our Process</h3>
    <div class="card-photo" role="img" aria-label="Photo of a laptop packed in a molded cardboard box" style="background:linear-gradient(135deg,#d9c7a7,#b79b6f 50%,#6a8f54)"></div>
    <ul class="card-list">
      <li><span class="dot"></span>Vestibulum ante ipsum primis in faucibus orci luctus.</li>
      <li><span class="dot"></span>etultrices posuere cubilia Curae; Suspendisse a tellus quis libero euismod egestas nam.dolor mauris.</li>
    </ul>
    <span class="more">Read more</span>
  </section>

  <section class="abs card" style="left:254px">
    <h3 class="card-head">Grow Your Business</h3>
    <div class="card-photo" role="img" aria-label="Photo of a printed cardboard shipping box" style="background:linear-gradient(135deg,#f1ece6,#c9a57a 55%,#a57f55)"></div>
    <ul class="card-list">
      <li><span class="dot"></span>Vestibulum ante ipsum primis in faucibus orci luctus.</li>
      <li><span class="dot"></span>etultrices posuere cubilia Curae; Suspendisse a tellus quis libero euismod egestas nam.dolor mauris.</li>
    </ul>
    <span class="more">Read more</span>
  </section>

  <section class="abs card" style="left:511px">
    <h3 class="card-head">Testimonials</h3>
    <div class="card-photo" role="img" aria-label="Photo of an open white product carton" style="background:linear-gradient(135deg,#e8e8e8,#cfcfcf 60%,#f4f4f4)"></div>
    <div class="testi"><span class="quote-mark">“</span><span>We are so much impressed by the HLS services They were so fantastic at job. Their print services are just amazing...</span></div>
    <p class="testi-name">Dana Ortiz, Business person</p>
    <span class="more">More testimonials</span>
  </section>

  <div class="abs divider"></div>
  <h2 class="abs clients-title">CLIENTS</h2>
  <div class="abs clients">
    <span class="client"><span class="c"></span>Loopwave</span>
    <span class="client"><span class="c"></span>Trailpoint</span>
    <span class="client"><span class="c"></span>Discora</span>
    <span class="client"><span class="c"></span>Paynest</span>
    <span class="client"><span class="c"></span>Berrylink</span>
    <span class="client"><span class="c"></span>Orchardia</span>
  </div>
</div>

<footer class="footer">
  <div class="fcol" style="left:224px">
    <h3>Contact Us</h3>
    <div class="contact-row"><svg width="11" height="13" viewBox="0 0 12 16"><path fill="#f0a21d" d="M6 0a6 6 0 0 0-6 6c0 4.5 6 10 6 10s6-5.5 6-10a6 6 0 0 0-6-6zm0 8.5a2.5 2.5 0 1 1 0-5 2.5 2.5 0 0 1 0 5z"/></svg><span>48 Alder Street West<br>Toronto, Ontario<br>M5V 0A1</span></div>
    <div class="contact-row" style="margin-top:8px"><svg width="12" height="12" viewBox="0 0 24 24"><path fill="#f0a21d" d="M6.6 10.8a15 15 0 0 0 6.6 6.6l2.2-2.2a1 1 0 0 1 1-.25 11 11 0 0 0 3.6.6 1 1 0 0 1 1 1V20a1 1 0 0 1-1 1A17 17 0 0 1 3 4a1 1 0 0 1 1-1h3.5a1 1 0 0 1 1 1c0 1.25.2 2.45.6 3.6a1 1 0 0 1-.25 1z"/></svg><span>123-345-5678</span></div>
    <div class="contact-row" style="margin-top:5px"><svg width="12" height="12" viewBox="0 0 12 12"><rect x="1" y="4" width="10" height="7" fill="#f0a21d"/><rect x="3" y="1" width="6" height="3" fill="#f0a21d"/></svg><span>123-345-5678</span></div>
    <div class="contact-row" style="margin-top:5px;font-size:12px"><svg width="12" height="9" viewBox="0 0 24 18"><rect width="24" height="18" rx="2" fill="#f0a21d"/><path d="M1 2l11 8 11-8" stroke="#8d6a4f" stroke-width="2" fill="none"/></svg><span>info@harborlaneSupply.com</span></div>
  </div>
  <div class="fcol" style="left:464px">
    <h3>Links</h3>
    <ul class="links"><li>Home</li><li>About Us</li><li>Printing Services</li><li>Operation Hours</li><li>Mission Statement</li><li>Locate Us</li><li>Client Login</li></ul>
  </div>
  <div class="fcol" style="left:627px">
    <h3>Social Links</h3>
    <div class="socials"><span style="background:#3b5c9a"></span><span style="background:#3aa6dc"></span><span style="background:#1f72a8"></span><span style="background:#f08a24"></span></div>
    <div class="like"><span>Like</span><span>162</span></div>
  </div>
  <div class="fcol" style="left:788px">
    <h3>Feedback</h3>
    <div class="finput">Name (required)</div>
    <div class="finput">Email (required)</div>
    <div class="finput" style="height:48px">Message (required)</div>
    <div class="fsubmit">SUBMIT</div>
  </div>
</footer>
<div class="footer-bottom">All Right Reserved 2015. Harbor Lane Supply.</div>
</body>
</html>
```